Sales presentation introduction for Finance and Tech firms

Our business is two fold - 1) recruitment 2) consultancy. We would like a one or two page template that we can use to send to potential clients. The template will ideally be the same for the recruitment and consultancy side. We need to be able to edit the template to enter text.

I have attached our logo so you can see what we currently use on Corvella.

Sector is financial services and technology. We do not intent to have lots of text but the layout/images/designs to be used should cover some of page in a way that it takes up some space to avoid having to write lot of text.

Open to colour suggestions.

Please look at the attached word doc to see the text I would like for the two presentations.

Happy to answer questions.

Target Market(s)

Directors

Industry/Entity Type

Finance and tech companies

Colors
0094D4
00A9DD
6FCCEA
C7EBF8
E9F6FB

Requirements
Must have
• Editable text

```html
<!DOCTYPE html>
<html lang="en">
<head>
<meta charset="utf-8">
<title>Veltrane – Consultancy &amp; Recruitment Sheets</title>
<link href="https://fonts.googleapis.com/css2?family=Oswald:wght@400;500;600&family=Roboto:wght@400;500;700&family=Roboto+Mono:wght@700&display=swap" rel="stylesheet">
<style>
  :root{
    --blue-deep:#0d4d99;
    --blue:#1663b8;
    --blue-bright:#0094d4;
    --blue-sky:#00a9dd;
    --blue-soft:#6fccea;
    --blue-pale:#c7ebf8;
    --blue-mist:#e9f6fb;
    --ink:#2c2c2e;
    --grey:#6b6b6e;
    --band:#3a3b3d;
    --canvas:#e4e4e4;
  }
  *{margin:0;padding:0;box-sizing:border-box}
  html,body{width:677px;height:1200px;overflow:hidden}
  body{background:var(--canvas);position:relative;font-family:"Roboto",sans-serif}
  .page{position:absolute;width:415px;height:578px;background:#fff;transform-origin:0 0;overflow:hidden;box-shadow:0 3px 10px rgba(0,0,0,.25)}
  .page--hero{left:98px;top:30px;transform:scale(1.1566)}
  .page--left{left:26px;top:740px;transform:scale(.7229)}
  .page--right{left:351px;top:740px;transform:scale(.7229)}
  .abs{position:absolute}
  .shape{position:absolute;left:0;top:0}
  .brand{font-family:"Oswald",sans-serif;font-weight:400;font-size:26px;color:#fff;letter-spacing:.5px}
  .tagline{font-family:"Oswald",sans-serif;font-weight:400;color:#fff;font-size:9.4px;line-height:1.42;text-transform:uppercase}
  .title{font-family:"Oswald",sans-serif;font-weight:500;color:var(--blue);text-transform:uppercase}
  .title--main{font-size:12.5px}
  .title--sub{font-size:11.5px;display:flex;align-items:center;gap:4px}
  .dot{width:9px;height:9px;border-radius:50%;background:var(--blue);display:inline-block}
  .body{font-size:4.3px;line-height:1.55;color:var(--grey)}
  .lead{font-size:5.4px;line-height:1.4;color:var(--ink);font-weight:700}
  .node-label{font-size:3.1px;line-height:1.25;color:var(--grey);text-align:center;width:36px}
  .web{font-family:"Roboto Mono",monospace;font-weight:700;color:#fff;font-size:9.5px;letter-spacing:1.4px}
  .contact{font-family:"Oswald",sans-serif;font-size:6.4px;color:var(--ink);display:flex;align-items:center;gap:4px;white-space:nowrap}
  .pill{left:42px;top:246px;width:330px;height:30px;border-radius:15px;background:var(--blue);color:#fff;font-size:5.6px;font-weight:500;text-align:center;line-height:1.55;padding-top:7px}
  .checks{list-style:none}
  .checks li{font-size:5.4px;font-weight:700;color:var(--blue);line-height:1.95}
  .checks li::before{content:"▲";font-size:3.6px;margin-right:3px;vertical-align:1px}
  .cloud span{position:absolute;white-space:nowrap;line-height:1;font-family:"Roboto",sans-serif}
</style>
</head>
<body>

<!-- Consultancy sheet, large -->
<section class="page page--hero">
  <svg class="shape" width="415" height="200" viewBox="0 0 415 200">
    <defs>
      <linearGradient id="heroNet" x1="0" y1="0" x2="1" y2="1">
        <stop offset="0" stop-color="#0a1b3d"/><stop offset=".45" stop-color="#1c5fb5"/><stop offset=".75" stop-color="#123d80"/><stop offset="1" stop-color="#0b1730"/>
      </linearGradient>
    </defs>
    <rect width="415" height="150" fill="#1b1e25"/>
    <rect x="140" width="275" height="150" fill="url(#heroNet)" role="img" aria-label="Glowing digital network of connected nodes over a city at night"/>
    <path d="M0,118 H205 C232,118 236,140 262,140 H415 V188 H0 Z" fill="var(--band)"/>
    <path d="M0,116 H205 C232,116 236,138 262,138 H415" fill="none" stroke="#d8d8d8" stroke-width="1"/>
    <line x1="0" y1="199" x2="415" y2="199" stroke="var(--blue-pale)" stroke-width="1.5"/>
  </svg>
  <div class="abs brand" style="left:16px;top:58px">VELTRANE</div>
  <p class="abs tagline" style="left:12px;top:123px;width:190px">A partner who brings new and innovative ideas to the table, through extensive industry experience and knowledge.</p>
  <p class="abs tagline" style="left:216px;top:157px;width:190px">Veltrane will ensure you are prepared for growth.</p>

  <h2 class="abs title title--main" style="left:12px;top:203px">Veltrane Consultancy</h2>
  <p class="abs body" style="left:12px;top:224px;width:392px">Veltrane Partners is a bespoke consultancy firm that specialises in buy side investment. Through an industry based consultative approach we assist our clients in preparing for and facilitating long term growth. Working closely with our clients we combine innovative thinking and breakthrough technologies to accelerate progress and, together, achieve enduring results.</p>
  <p class="abs body" style="left:12px;top:246px;width:392px">Experienced in successfully delivering change for global organisations as well as assisting smaller firms during their growth phase. Veltrane will work with you to create a workable model and ensure successful delivery of the project.</p>

  <svg class="shape" style="top:268px" width="415" height="60" viewBox="0 0 415 60">
    <path d="M28,26 V14 H387 V26" fill="none" stroke="var(--blue)" stroke-width="1"/>
    <path d="M25,24 L28,29 L31,24 Z M384,24 L387,29 L390,24 Z" fill="var(--blue)"/>
    <g fill="var(--blue)">
      <circle cx="28" cy="44" r="12"/><circle cx="73" cy="44" r="12"/><circle cx="118" cy="44" r="12"/>
      <circle cx="163" cy="44" r="12"/><circle cx="208" cy="44" r="12"/><circle cx="253" cy="44" r="12"/>
      <circle cx="298" cy="44" r="12"/><circle cx="343" cy="44" r="12"/><circle cx="387" cy="44" r="12"/>
    </g>
    <g fill="none" stroke="#fff" stroke-width=".9">
      <rect x="22" y="38" width="12" height="11"/><rect x="67" y="38" width="12" height="9"/><rect x="112" y="38" width="12" height="11"/>
      <rect x="157" y="39" width="12" height="8"/><path d="M202,48 A6,6 0 0 1 214,48"/><rect x="248" y="37" width="10" height="13"/>
      <rect x="292" y="38" width="10" height="11"/><rect x="381" y="38" width="12" height="11"/><rect x="337" y="38" width="12" height="11"/>
    </g>
  </svg>
  <div class="abs" style="top:327px;left:10px;display:flex;gap:9px">
    <span class="node-label">Order Management and Trading</span><span class="node-label">Investment and Research</span><span class="node-label">Static, Pricing and Benchmark Data</span>
    <span class="node-label">CRM/ Onboarding</span><span class="node-label">Performance, Risk and Attribution</span><span class="node-label">Client and Regulatory Reporting</span>
    <span class="node-label">Compliance</span><span class="node-label">Finance and Accounting</span><span class="node-label">Middle and Back Office</span>
  </div>

  <h3 class="abs title title--sub" style="left:12px;top:368px"><i class="dot"></i>Business Strategy</h3>
  <p class="abs body" style="left:12px;top:387px;width:182px">Veltrane will help you create a business strategy tailored to your requirements. Ensuring each business process is defined and taken into account allows for a successful design. Creating and implementing an operating model that takes into account budget, resources, culture and your company's vision.</p>
  <h3 class="abs title title--sub" style="left:216px;top:368px"><i class="dot"></i>Change Management</h3>
  <p class="abs body" style="left:216px;top:387px;width:188px">Veltrane works with clients to deliver bespoke change initiatives. Rigorous business analysis and risk management allows for successful change initiatives. We work with you throughout the complete process, to ensure that delivery is based on value. Transition phases are challenging aspects of change initiatives which is why our team manage all transitions and the risk they carry.</p>
  <h3 class="abs title title--sub" style="left:12px;top:444px"><i class="dot"></i>IT Transformation</h3>
  <p class="abs body" style="left:12px;top:463px;width:182px">Veltrane is widely experienced in a range of technologies. We help with the implementation of software provider or design and develop bespoke services. Covering front to back office the team specialises in full project lifecycle from feasibility through to implementation.</p>
  <h3 class="abs title title--sub" style="left:216px;top:444px"><i class="dot"></i>Organisational Structure</h3>
  <p class="abs body" style="left:216px;top:463px;width:188px">Veltrane works with clients to improve resource capability and strategic partnerships. Acting as an extension of the HR function, we analyse business processes and ensure that our clients have the ability to manage changing workforce demands.</p>

  <svg class="shape" style="top:518px" width="415" height="60" viewBox="0 0 415 60">
    <rect y="4" width="415" height="56" fill="var(--blue-pale)"/>
    <path d="M0,4 H166 L154,28 H0 Z" fill="var(--blue-deep)"/>
  </svg>
  <div class="abs web" style="left:12px;top:526px">www.veltranepartners.com</div>
  <div class="abs contact" style="right:12px;top:558px">
    <svg width="7" height="6" viewBox="0 0 7 6"><path d="M3.5,0 L7,6 H0 Z" fill="var(--blue)"/></svg>
    London, United Kingdom | info@veltranepartners.com | +44 (0) 7700 900418
  </div>
</section>

<!-- Consultancy sheet, small -->
<section class="page page--left">
  <svg class="shape" width="415" height="200" viewBox="0 0 415 200">
    <defs>
      <linearGradient id="heroNet2" x1="0" y1="0" x2="1" y2="1">
        <stop offset="0" stop-color="#0a1b3d"/><stop offset=".45" stop-color="#1c5fb5"/><stop offset=".75" stop-color="#123d80"/><stop offset="1" stop-color="#0b1730"/>
      </linearGradient>
    </defs>
    <rect width="415" height="150" fill="#1b1e25"/>
    <rect x="140" width="275" height="150" fill="url(#heroNet2)" role="img" aria-label="Glowing digital network of connected nodes over a city at night"/>
    <path d="M0,118 H205 C232,118 236,140 262,140 H415 V188 H0 Z" fill="var(--band)"/>
    <path d="M0,116 H205 C232,116 236,138 262,138 H415" fill="none" stroke="#d8d8d8" stroke-width="1"/>
    <line x1="0" y1="199" x2="415" y2="199" stroke="var(--blue-pale)" stroke-width="1.5"/>
  </svg>
  <div class="abs brand" style="left:16px;top:58px">VELTRANE</div>
  <p class="abs tagline" style="left:12px;top:123px;width:190px">A partner who brings new and innovative ideas to the table, through extensive industry experience and knowledge.</p>
  <p class="abs tagline" style="left:216px;top:157px;width:190px">Veltrane will ensure you are prepared for growth.</p>

  <h2 class="abs title title--main" style="left:12px;top:203px">Veltrane Consultancy</h2>
  <p class="abs body" style="left:12px;top:224px;width:392px">Veltrane Partners is a bespoke consultancy firm that specialises in buy side investment. Through an industry based consultative approach we assist our clients in preparing for and facilitating long term growth. Working closely with our clients we combine innovative thinking and breakthrough technologies to accelerate progress and, together, achieve enduring results.</p>
  <p class="abs body" style="left:12px;top:246px;width:392px">Experienced in successfully delivering change for global organisations as well as assisting smaller firms during their growth phase. Veltrane will work with you to create a workable model and ensure successful delivery of the project.</p>

  <svg class="shape" style="top:268px" width="415" height="60" viewBox="0 0 415 60">
    <path d="M28,26 V14 H387 V26" fill="none" stroke="var(--blue)" stroke-width="1"/>
    <path d="M25,24 L28,29 L31,24 Z M384,24 L387,29 L390,24 Z" fill="var(--blue)"/>
    <g fill="var(--blue)">
      <circle cx="28" cy="44" r="12"/><circle cx="73" cy="44" r="12"/><circle cx="118" cy="44" r="12"/>
      <circle cx="163" cy="44" r="12"/><circle cx="208" cy="44" r="12"/><circle cx="253" cy="44" r="12"/>
      <circle cx="298" cy="44" r="12"/><circle cx="343" cy="44" r="12"/><circle cx="387" cy="44" r="12"/>
    </g>
    <g fill="none" stroke="#fff" stroke-width=".9">
      <rect x="22" y="38" width="12" height="11"/><rect x="67" y="38" width="12" height="9"/><rect x="112" y="38" width="12" height="11"/>
      <rect x="157" y="39" width="12" height="8"/><path d="M202,48 A6,6 0 0 1 214,48"/><rect x="248" y="37" width="10" height="13"/>
      <rect x="292" y="38" width="10" height="11"/><rect x="381" y="38" width="12" height="11"/><rect x="337" y="38" width="12" height="11"/>
    </g>
  </svg>
  <div class="abs" style="top:327px;left:10px;display:flex;gap:9px">
    <span class="node-label">Order Management and Trading</span><span class="node-label">Investment and Research</span><span class="node-label">Static, Pricing and Benchmark Data</span>
    <span class="node-label">CRM/ Onboarding</span><span class="node-label">Performance, Risk and Attribution</span><span class="node-label">Client and Regulatory Reporting</span>
    <span class="node-label">Compliance</span><span class="node-label">Finance and Accounting</span><span class="node-label">Middle and Back Office</span>
  </div>

  <h3 class="abs title title--sub" style="left:12px;top:368px"><i class="dot"></i>Business Strategy</h3>
  <p class="abs body" style="left:12px;top:387px;width:182px">Veltrane will help you create a business strategy tailored to your requirements. Ensuring each business process is defined and taken into account allows for a successful design. Creating and implementing an operating model that takes into account budget, resources, culture and your company's vision.</p>
  <h3 class="abs title title--sub" style="left:216px;top:368px"><i class="dot"></i>Change Management</h3>
  <p class="abs body" style="left:216px;top:387px;width:188px">Veltrane works with clients to deliver bespoke change initiatives. Rigorous business analysis and risk management allows for successful change initiatives. We work with you throughout the complete process, to ensure that delivery is based on value. Transition phases are challenging aspects of change initiatives which is why our team manage all transitions and the risk they carry.</p>
  <h3 class="abs title title--sub" style="left:12px;top:444px"><i class="dot"></i>IT Transformation</h3>
  <p class="abs body" style="left:12px;top:463px;width:182px">Veltrane is widely experienced in a range of technologies. We help with the implementation of software provider or design and develop bespoke services. Covering front to back office the team specialises in full project lifecycle from feasibility through to implementation.</p>
  <h3 class="abs title title--sub" style="left:216px;top:444px"><i class="dot"></i>Organisational Structure</h3>
  <p class="abs body" style="left:216px;top:463px;width:188px">Veltrane works with clients to improve resource capability and strategic partnerships. Acting as an extension of the HR function, we analyse business processes and ensure that our clients have the ability to manage changing workforce demands.</p>

  <svg class="shape" style="top:518px" width="415" height="60" viewBox="0 0 415 60">
    <rect y="4" width="415" height="56" fill="var(--blue-pale)"/>
    <path d="M0,4 H166 L154,28 H0 Z" fill="var(--blue-deep)"/>
  </svg>
  <div class="abs web" style="left:12px;top:526px">www.veltranepartners.com</div>
  <div class="abs contact" style="right:12px;top:558px">
    <svg width="7" height="6" viewBox="0 0 7 6"><path d="M3.5,0 L7,6 H0 Z" fill="var(--blue)"/></svg>
    London, United Kingdom | info@veltranepartners.com | +44 (0) 7700 900418
  </div>
</section>

<!-- Recruitment sheet, small -->
<section class="page page--right">
  <svg class="shape" width="415" height="130" viewBox="0 0 415 130">
    <defs>
      <linearGradient id="darkTexture" x1="0" y1="0" x2="1" y2="1">
        <stop offset="0" stop-color="#2a2b2e"/><stop offset=".6" stop-color="#44464a"/><stop offset="1" stop-color="#2d2e31"/>
      </linearGradient>
    </defs>
    <rect width="415" height="118" fill="url(#darkTexture)" role="img" aria-label="Dark textured abstract header background"/>
    <path d="M0,96 H150 C178,96 182,110 208,110 H415 V130 H0 Z" fill="#fff"/>
    <path d="M0,96 H150 C178,96 182,110 208,110 H415" fill="none" stroke="var(--blue)" stroke-width="3"/>
    <path d="M0,91 H150 C178,91 182,105 208,105 H415" fill="none" stroke="#8a8b8e" stroke-width="1.2"/>
  </svg>
  <div class="abs brand" style="left:286px;top:52px">VELTRANE</div>

  <h2 class="abs title" style="left:12px;top:110px;font-size:11px">Veltrane Recruitment</h2>
  <p class="abs lead" style="left:12px;top:138px;width:392px">A partner who brings new and innovative ideas to the table, through extensive industry experience and knowledge. Veltrane will ensure you are prepared for growth.</p>
  <p class="abs body" style="left:12px;top:160px;width:392px">Veltrane is more than an ordinary recruitment service. Our experts work with clients to develop a HR strategy that maps current and impending organisational needs, using research to effectively benchmark. We are developing various talent communities that provide effective and timely recruitment solutions for our clients.</p>
  <p class="abs body" style="left:12px;top:188px;width:392px">Specialists in Asset Management recruitment with a specialisation in IT, Operations, Regulation and Change Management.</p>
  <p class="abs body" style="left:12px;top:203px;width:392px">Veltrane acts as an extension of your HR function, providing an end-to-end permanent and contingent talent acquisition solution, taking full accountability and ownership for the entire recruitment process, which includes:</p>
  <div class="abs pill">▲ Workforce Planning &nbsp;▲ Strategic Sourcing &nbsp;▲ Talent Engagement<br>▲ Candidate Management &nbsp;▲ Weekly Vacancy Updates</div>
  <p class="abs body" style="left:12px;top:284px;width:392px">We recognise that hiring can be a lengthy process, therefore we partner with you to ensure you only interview top quality candidates, cutting out multiple meetings with multiple candidates. Giving hiring managers time back in their diaries to do their day jobs and reducing the time to hire.</p>
  <ul class="abs checks" style="left:12px;top:303px">
    <li>Understanding the roles, and partnering with you to build meaningful job descriptions</li>
    <li>Candidates are fully screened and interviewed prior to presentation to you</li>
    <li>Qualified shortlist of top 3 candidates</li>
    <li>Support with interviews and we ensure the candidate has a positive experience</li>
  </ul>
  <p class="abs lead" style="left:12px;top:374px;width:392px;font-size:5.2px">Veltrane recruitment partners with principal business consultants from Veltrane consultancy to ensure candidates are properly screened before presenting to our clients. This allows for our clients to focus on only interviewing the best on the market.</p>

  <div class="abs cloud" style="left:0;top:0;width:415px;height:578px">
    <span style="left:38px;top:428px;font-size:9px;color:var(--blue)">Pricing and</span>
    <span style="left:44px;top:438px;font-size:9px;color:var(--blue)">Analytics</span>
    <span style="left:108px;top:420px;font-size:25px;color:var(--blue)">XML</span>
    <span style="left:172px;top:425px;font-size:10px;color:var(--blue)">Fixed Income</span>
    <span style="left:266px;top:418px;font-size:20px;color:var(--blue-sky)">MIS</span>
    <span style="left:24px;top:453px;font-size:8px;color:var(--blue-sky)">Connectivity</span>
    <span style="left:73px;top:451px;font-size:9.5px;color:var(--blue)">Reference Data</span>
    <span style="left:183px;top:470px;font-size:8px;color:var(--blue);transform:rotate(-90deg);transform-origin:0 0">Equity</span>
    <span style="left:198px;top:444px;font-size:19px;color:var(--blue)">SQL</span>
    <span style="left:250px;top:446px;font-size:8px;color:var(--blue)">Workflow Management</span>
    <span style="left:262px;top:455px;font-size:8.5px;color:var(--blue)">Collateral</span>
    <span style="left:34px;top:464px;font-size:11px;color:var(--blue-sky)">Business Intelligence</span>
    <span style="left:198px;top:463px;font-size:12px;color:var(--blue)">NoSQL</span>
    <span style="left:243px;top:465px;font-size:8px;color:var(--blue)">Management</span>
    <span style="left:22px;top:479px;font-size:10px;color:var(--blue)">Settlement Risk and attribution</span>
    <span style="left:232px;top:475px;font-size:15px;font-weight:700;color:var(--blue)">FIX/API</span>
    <span style="left:331px;top:477px;font-size:8px;color:var(--blue)">Batch</span>
    <span style="left:326px;top:485px;font-size:8px;color:var(--blue)">Processing</span>
  </div>

  <svg class="shape" style="top:518px" width="415" height="60" viewBox="0 0 415 60">
    <rect y="4" width="415" height="56" fill="var(--blue-pale)"/>
    <path d="M0,4 H166 L154,28 H0 Z" fill="var(--blue-deep)"/>
  </svg>
  <div class="abs web" style="left:12px;top:526px">www.veltranepartners.com</div>
  <div class="abs contact" style="right:12px;top:558px">
    <svg width="7" height="6" viewBox="0 0 7 6"><path d="M3.5,0 L7,6 H0 Z" fill="var(--blue)"/></svg>
    London, United Kingdom | info@veltranepartners.com | +44 (0) 7700 900418
  </div>
</section>

</body>
</html>
```